BOLD & MINIMALIST DESIGN NEEDED

We want a very bold but minimalistic business card design that is impactful and utilizes both sides of the business card. Our current logo is included for your use.

We want bold fonts and good use of negative space. We don't want the logo to overpower the design.

Target Market(s)

Professionals who are building new commercial buildings.

Industry/Entity Type

Construction

Contact Information for Business Card

Name, Title, email, office phone, cell phone, website

Font styles to use
Serif
Sans Serif

Requirements
Must have
• Bold design!

```html
<!DOCTYPE html>
<html lang="en">
<head>
<meta charset="utf-8">
<title>Ridgeline Design + Build – Business Card</title>
<link rel="stylesheet" href="https://fonts.googleapis.com/css2?family=Montserrat:wght@300;400;700;800&display=swap">
<style>
  :root {
    --backdrop: #dcdcdc;
    --card-light: #ffffff;
    --card-dark: #0c0d0f;
    --ink: #0c0d0f;
    --paper: #ffffff;
    --accent: #8fcb54;
  }
  * { margin: 0; padding: 0; box-sizing: border-box; }
  html, body {
    width: 1200px; height: 1200px; overflow: hidden;
    background: var(--backdrop);
    font-family: "Montserrat", Arial, sans-serif;
  }
  .card {
    position: absolute; left: 179px; width: 861px; height: 496px; overflow: hidden;
  }
  .card--front { top: 84px; background: var(--card-light); }
  .card--back { top: 621px; background: var(--card-dark); color: var(--paper); }

  .wordmark {
    font-weight: 800; text-transform: uppercase; line-height: 1;
  }
  .wordmark__name { display: block; letter-spacing: 0.01em; }
  .wordmark__tag { display: block; letter-spacing: 0.32em; }

  .card--front .wordmark {
    position: absolute; left: 0; right: 0; top: 176px;
    text-align: center; color: var(--ink);
  }
  .card--front .wordmark__name { font-size: 70px; }
  .card--front .wordmark__tag { font-size: 21px; margin-top: 12px; padding-left: 0.32em; }

  .card--back .wordmark {
    position: absolute; left: 36px; top: 44px; color: var(--paper);
  }
  .card--back .wordmark__name { font-size: 58px; }
  .card--back .wordmark__tag { font-size: 19px; margin-top: 10px; }

  .holder {
    position: absolute; right: 48px; top: 178px; text-align: right;
  }
  .holder__name { font-weight: 800; font-size: 29px; letter-spacing: 0.01em; }
  .holder__title { font-weight: 400; font-size: 25px; color: var(--accent); margin-top: 8px; letter-spacing: 0.04em; }

  .contacts {
    position: absolute; left: 36px; top: 328px; list-style: none;
  }
  .contacts__item {
    display: flex; align-items: center; height: 35px;
    font-weight: 300; font-size: 23px; letter-spacing: 0.04em;
  }
  .contacts__icon { width: 26px; height: 26px; margin-right: 14px; flex: none; }
  .contacts__accent { color: var(--accent); }

  .roof { position: absolute; left: 0; top: 0; }
</style>
</head>
<body>

<section class="card card--front" aria-label="Card front">
  <div class="wordmark">
    <span class="wordmark__name">Ridgeline</span>
    <span class="wordmark__tag">Design + Build</span>
  </div>
</section>

<section class="card card--back" aria-label="Card back">
  <svg class="roof" width="861" height="496" viewBox="0 0 861 496" aria-hidden="true">
    <polygon points="340,496 674,312 861,414 861,496" fill="var(--paper)"/>
    <polygon points="362,496 674,324 861,422 861,496" fill="var(--accent)"/>
    <polygon points="398,496 674,342 861,432 861,496" fill="var(--paper)"/>
  </svg>

  <div class="wordmark">
    <span class="wordmark__name">Ridgeline</span>
    <span class="wordmark__tag">Design + Build</span>
  </div>

  <div class="holder">
    <p class="holder__name">Name Surename</p>
    <p class="holder__title">Director</p>
  </div>

  <ul class="contacts">
    <li class="contacts__item">
      <svg class="contacts__icon" viewBox="0 0 24 24" aria-hidden="true">
        <path d="M6.6 10.8a15 15 0 0 0 6.6 6.6l2.2-2.2c.3-.3.7-.4 1-.2 1.1.4 2.3.6 3.6.6.6 0 1 .4 1 1V20c0 .6-.4 1-1 1A17 17 0 0 1 3 4c0-.6.4-1 1-1h3.5c.6 0 1 .4 1 1 0 1.3.2 2.5.6 3.6.1.3 0 .7-.2 1z" fill="var(--accent)"/>
        <path d="M14 3a7 7 0 0 1 7 7M14 6.5a3.5 3.5 0 0 1 3.5 3.5" fill="none" stroke="var(--accent)" stroke-width="1.6"/>
      </svg>
      555-014-3870
    </li>
    <li class="contacts__item">
      <svg class="contacts__icon" viewBox="0 0 24 24" aria-hidden="true">
        <path d="M2 8c0-2 4.5-3.5 10-3.5S22 6 22 8v1.5h-5V8H7v1.5H2z" fill="var(--accent)"/>
        <path d="M7 10h10l3 4v6H4v-6z" fill="var(--accent)"/>
        <circle cx="12" cy="15" r="2.4" fill="var(--card-dark)"/>
      </svg>
      555-014-3870
    </li>
    <li class="contacts__item">
      <svg class="contacts__icon" viewBox="0 0 24 24" aria-hidden="true">
        <rect x="2" y="5" width="20" height="14" fill="var(--accent)"/>
        <path d="M2 5l10 8 10-8M2 19l7.5-7M22 19l-7.5-7" fill="none" stroke="var(--card-dark)" stroke-width="1.4"/>
      </svg>
      info@ridgeline-db.com
    </li>
    <li class="contacts__item">
      <svg class="contacts__icon" viewBox="0 0 24 24" aria-hidden="true">
        <g fill="none" stroke="var(--accent)" stroke-width="1.6">
          <circle cx="12" cy="12" r="10"/>
          <ellipse cx="12" cy="12" rx="4.5" ry="10"/>
          <path d="M2 12h20M4 6.5h16M4 17.5h16M12 2v20"/>
        </g>
      </svg>
      <span>www.<span class="contacts__accent">ridgeline-db</span>.com</span>
    </li>
  </ul>
</section>

</body>
</html>
```